Modern Business Card For A Digital Advertising Company

I'll be print on the Pell Prints Velour paper http://us.pellprints.com/products/velour/business-cards.html
Need's to be modern and use the color palette of the logo or gray scales. I think integrating the pixelation of the logo in to the card and having it wrap from one side to the other could be interesting. My company provides ad operations, web development, and number of other services to websites around the world. You can see my website at http://www.zantorhq.com
Contact info on the card needs to have
Owen Lasko
President
p.318.204.6637
owen@zantorhq.com
http://www.zantorhq.com
Doesn't necessarily need to be in that order
Website owners
Business

```html
<!DOCTYPE html>
<html lang="en">
<head>
<meta charset="utf-8">
<title>Owen Lasko – Zantor HQ Business Card</title>
<link rel="stylesheet" href="https://fonts.googleapis.com/css2?family=Roboto+Condensed:wght@700;800&family=Arimo:wght@700&display=swap">
<style>
  :root {
    --card-white: #ffffff;
    --pale-green: #e3efd0;
    --pale-green-soft: #edf5e1;
    --deep-green: #1b6a40;
    --leaf-green: #5db63d;
    --logo-green: #8cc63f;
    --logo-gray: #3f3f3f;
    --frame-gray: #3a3a3a;
  }
  html, body {
    margin: 0;
    padding: 0;
    width: 1200px;
    height: 735px;
    overflow: hidden;
    background: var(--card-white);
  }
  .card {
    position: relative;
    width: 1200px;
    height: 735px;
    box-sizing: border-box;
    border: 2px solid var(--frame-gray);
    background: var(--card-white);
    overflow: hidden;
  }
  .card-backdrop {
    position: absolute;
    inset: 0;
    width: 100%;
    height: 100%;
  }
  .brand {
    position: absolute;
    top: 52px;
    right: 68px;
    display: flex;
    flex-direction: column;
    align-items: flex-end;
    gap: 14px;
  }
  .brand-square {
    width: 96px;
    height: 96px;
    background: var(--logo-green);
  }
  .brand-name {
    font-family: "Arimo", Arial, sans-serif;
    font-weight: 700;
    font-size: 30px;
    letter-spacing: 2px;
    color: var(--logo-gray);
    line-height: 1;
  }
  .identity {
    position: absolute;
    left: 78px;
    top: 302px;
  }
  .person-name {
    margin: 0;
    font-family: "Roboto Condensed", "Arial Narrow", sans-serif;
    font-weight: 800;
    font-size: 84px;
    line-height: 1;
    letter-spacing: -0.5px;
    color: var(--deep-green);
  }
  .person-title {
    margin: 2px 0 0 8px;
    font-family: "Arimo", Arial, sans-serif;
    font-weight: 700;
    font-size: 45px;
    line-height: 1.1;
    color: var(--leaf-green);
  }
  .contact {
    position: absolute;
    right: 68px;
    top: 522px;
    margin: 0;
    font-family: "Arimo", Arial, sans-serif;
    font-weight: 700;
    font-size: 31px;
    color: var(--deep-green);
    text-align: right;
    font-style: normal;
    line-height: 1;
  }
  .contact-phone { display: block; margin-bottom: 38px; padding-right: 12px; }
  .contact-email { display: block; margin-bottom: 10px; }
  .contact-web { display: block; }
</style>
</head>
<body>
  <main class="card">
    <svg class="card-backdrop" viewBox="0 0 1200 735" aria-hidden="false">
      <defs>
        <linearGradient id="mosaic-fade" x1="0" y1="0" x2="1" y2="0">
          <stop offset="0" stop-color="#e3efd0" stop-opacity="0.55"/>
          <stop offset="0.6" stop-color="#dcebc6" stop-opacity="0.9"/>
          <stop offset="1" stop-color="#e3efd0" stop-opacity="0.7"/>
        </linearGradient>
      </defs>
      <g class="backdrop-bands">
        <polygon points="0,0 165,0 170,28 22,518 0,520" fill="var(--pale-green)"/>
        <polygon points="1070,0 1200,0 1200,340 1180,330" fill="var(--pale-green)"/>
        <polygon points="165,0 1070,0 1180,330 1120,338" fill="var(--card-white)"/>
      </g>
      <g class="pixel-mosaic" role="img" aria-label="Pixel mosaic of pale green squares sweeping across the lower right of the card">
        <polygon points="1200,360 1200,735 100,735 110,670 360,600 520,520 760,440 960,390" fill="url(#mosaic-fade)"/>
      </g>
    </svg>

    <div class="brand">
      <div class="brand-square"></div>
      <span class="brand-name">ZANTOR HQ</span>
    </div>

    <section class="identity">
      <h1 class="person-name">Owen Lasko</h1>
      <p class="person-title">President</p>
    </section>

    <address class="contact">
      <span class="contact-phone">p.318.204.6637</span>
      <span class="contact-email">owen@zantorhq.com</span>
      <span class="contact-web">http://www.zantorhq.com</span>
    </address>
  </main>
</body>
</html>
```